Mobile Fitness snd Therapy Business Card Design

I need a business card designed for my mobile fitness and therapy business.

Please view the images that I have uploaded. I like the simplicity of the design that I have attached. I adapted it with my information

Target Market(s)

Those seeking personal training, injury rehabilitation or massage therapy.

Industry/Entity Type

Business

Contact Information for Business Card

Derek Fulham - MSc, CAT(C), RMT, CSCS, Pn2
e-mail: derek@vantrelo.com
website: www.vantrelo.com
instagram: @derek_fulham

Font styles to use
Sans Serif

Colors
3176b5
0355a3

Requirements
Must have
• "Contact us to receive a FREE assessment"
• Services offered:
• Personal Training
• Golf Fitness
• Injury Rehab
• Massage Therapy
• Yoga
Nice to have
• Consistent colours with brand
• - Dark Blue: #232837
• - Blue: #5096f0
• Consistent look/feel with the website: www.vantrelo.com

```html
<!DOCTYPE html>
<html lang="en">
<head>
<meta charset="utf-8">
<title>Vantrelo Business Card</title>
<link rel="stylesheet" href="https://fonts.googleapis.com/css2?family=Montserrat:wght@600;700&family=Roboto:wght@400;500&family=Roboto+Condensed:wght@500;700&display=swap">
<style>
  :root {
    --backdrop: #e3e3e3;
    --navy: #232837;
    --paper: #f1f1f1;
    --blue: #2a5bd7;
    --blue-light: #5096f0;
    --ink: #3a3a3a;
    --white: #ffffff;
  }
  * { margin: 0; padding: 0; box-sizing: border-box; }
  html, body {
    width: 1200px; height: 960px; overflow: hidden;
    background: var(--backdrop);
  }
  .card {
    position: absolute;
    width: 600px; height: 343px;
    overflow: hidden;
  }
  .card--front { left: 314px; top: 113px; background: var(--paper); }
  .card--back { left: 311px; top: 472px; background: var(--navy); }

  .brand {
    position: absolute; left: 0; right: 0;
    text-align: center; color: var(--white);
  }
  .brand__name {
    display: block;
    font-family: "Montserrat", sans-serif;
    font-weight: 600;
    font-size: 46px;
    letter-spacing: 4px;
    line-height: 1;
  }
  .brand__tagline {
    display: block;
    margin-top: 10px;
    font-family: "Montserrat", sans-serif;
    font-weight: 700;
    font-size: 15.5px;
    letter-spacing: 2.2px;
  }

  .front__band {
    position: absolute; left: 0; top: 0;
    width: 100%; height: 169px;
    background: var(--navy);
  }
  .front__band .brand { top: 54px; }

  .person { position: absolute; left: 70px; top: 228px; }
  .person__name {
    font-family: "Roboto Condensed", sans-serif;
    font-weight: 500; font-size: 22px;
    color: var(--blue); line-height: 1;
  }
  .person__credentials {
    margin-top: 4px;
    font-family: "Roboto Condensed", sans-serif;
    font-weight: 500; font-size: 11px;
    color: var(--blue);
  }

  .contact { position: absolute; left: 363px; top: 226px; list-style: none; }
  .contact__item {
    display: flex; align-items: center; gap: 7px;
    font-family: "Roboto", sans-serif;
    font-size: 14.5px; color: var(--ink);
    height: 19.5px;
  }
  .contact__icon { width: 14px; height: 14px; flex: none; }

  .back .brand { top: 120px; }
  .cta {
    position: absolute; left: 59px; top: 259px;
    width: 483px; height: 34px;
    border-radius: 17px;
    background: var(--blue);
    color: var(--white);
    font-family: "Roboto Condensed", sans-serif;
    font-weight: 700; font-size: 20.5px;
    text-align: center; line-height: 34px;
  }
  .services {
    position: absolute; left: 0; right: 0; top: 298px;
    text-align: center;
    font-family: "Roboto", sans-serif;
    font-size: 14.5px; color: var(--white);
  }
  .services__sep { color: var(--blue-light); margin: 0 3px; }
</style>
</head>
<body>
  <section class="card card--front">
    <div class="front__band">
      <div class="brand">
        <span class="brand__name">VANTRELO</span>
        <span class="brand__tagline">NUTRITION - FITNESS - HEALTH</span>
      </div>
    </div>
    <div class="person">
      <p class="person__name">DEREK FULHAM</p>
      <p class="person__credentials">MSC, CAT(C), RMT, CSCS, PN2</p>
    </div>
    <ul class="contact">
      <li class="contact__item">
        <svg class="contact__icon" viewBox="0 0 14 14" aria-hidden="true">
          <rect x="1" y="3" width="12" height="8.5" rx="1" fill="#2a5bd7"/>
          <path d="M1.5 3.8 L7 8 L12.5 3.8" fill="none" stroke="#f1f1f1" stroke-width="1.1"/>
        </svg>
        derek@vantrelo.com
      </li>
      <li class="contact__item">
        <svg class="contact__icon" viewBox="0 0 14 14" aria-hidden="true">
          <circle cx="7" cy="7" r="6" fill="#2a5bd7"/>
          <ellipse cx="7" cy="7" rx="2.5" ry="6" fill="none" stroke="#f1f1f1" stroke-width="0.9"/>
          <line x1="1" y1="7" x2="13" y2="7" stroke="#f1f1f1" stroke-width="0.9"/>
        </svg>
        www.vantrelo.com
      </li>
      <li class="contact__item">
        <svg class="contact__icon" viewBox="0 0 14 14" aria-hidden="true">
          <circle cx="7" cy="7" r="6.5" fill="#2a5bd7"/>
        </svg>
        @derek_fulham
      </li>
    </ul>
  </section>

  <section class="card card--back back">
    <div class="brand">
      <span class="brand__name">VANTRELO</span>
      <span class="brand__tagline">NUTRITION - FITNESS - HEALTH</span>
    </div>
    <p class="cta">CONTACT US TO RECEIVE A FREE ASSESSMENT</p>
    <p class="services">Personal Training<span class="services__sep">|</span>Golf Fitness<span class="services__sep">|</span>Injury Rehab<span class="services__sep">|</span>Massage Therapy<span class="services__sep">|</span>Yoga</p>
  </section>
</body>
</html>
```